Building Referrer Relationships Booklet

4 page A4 booklet to give to potential professional referrers to establish a collaborative relationship.Needs to be bright, vibrant, colourful, friendly, inviting, in keeping with The Linden Practice colours.
Want to provide potential referrer partners a great reason to choose to collaborate with us. They need to know who we are, what makes us different/appealing, and who we are looking for to connect with.
The final product should communicate high performance and connectedness.
Updates

Target Market(s)

professional medical allied health and fitness practitioners

Industry/Entity Type

Health

Requirements
Must have
• energetic, vibrant, engaging, inviting, images

```html
<!DOCTYPE html>
<html lang="en">
<head>
<meta charset="utf-8">
<title>Referral Partners Required – The Linden Practice</title>
<link rel="stylesheet" href="https://fonts.googleapis.com/css2?family=Arimo:wght@400;700&display=swap">
<style>
  :root {
    --orange: #f0601c;
    --heading-orange: #e2531a;
    --ink: #111111;
    --paper: #ffffff;
    --rule: #f4f4f4;
    --photo-light: #eceef0;
    --photo-mid: #d7d2cd;
    --photo-skin: #e6c2ad;
    --partner-ink: #6a6a6a;
  }
  * { margin: 0; padding: 0; box-sizing: border-box; }
  html, body { width: 1200px; height: 900px; overflow: hidden; background: var(--paper); }
  body { font-family: "Arimo", Arial, sans-serif; color: var(--ink); }

  .page { position: relative; width: 1200px; height: 900px; overflow: hidden; }

  .hero-photo {
    position: absolute; left: 0; top: 0; width: 555px; height: 900px;
    background:
      radial-gradient(ellipse 420px 280px at 250px 560px, var(--photo-skin) 0%, rgba(230,194,173,0.55) 45%, rgba(230,194,173,0) 75%),
      linear-gradient(180deg, var(--photo-light) 0%, #e4e5e7 35%, var(--photo-mid) 70%, #c9c2bb 100%);
  }

  .hero-rule {
    position: absolute; left: 62px; width: 435px; height: 4px;
    background: var(--rule); box-shadow: 0 1px 3px rgba(0,0,0,0.2);
  }
  .hero-rule.top { top: 20px; }
  .hero-rule.bottom { top: 297px; }

  .hero-title {
    position: absolute; left: 62px; top: 72px; width: 440px;
    text-align: center; color: var(--orange);
    font-weight: 700; font-size: 72px; line-height: 66px; letter-spacing: 1px;
    text-shadow: 0 2px 6px rgba(0,0,0,0.25);
  }

  .section-heading {
    position: absolute; left: 555px; width: 645px; text-align: center;
    color: var(--heading-orange); font-weight: 700; font-size: 19.5px; letter-spacing: 0.3px;
  }

  .partner-item { position: absolute; left: 569px; width: 620px; }
  .partner-item::before {
    content: ""; position: absolute; left: 0; top: 0; width: 34px; height: 38px;
    background: var(--orange);
  }
  .partner-item h3, .partner-item p { margin-left: 44px; font-size: 15px; line-height: 19px; }
  .partner-item h3 { font-weight: 700; letter-spacing: 0.2px; }
  .partner-item p { font-weight: 400; }

  .partner-bar {
    position: absolute; left: 520px; top: 806px; width: 700px; height: 110px;
    background: var(--paper); border-radius: 14px;
    box-shadow: 0 -6px 14px rgba(0,0,0,0.25);
    display: flex; align-items: center; gap: 28px; padding: 0 0 14px 34px;
  }
  .partner-name {
    display: flex; align-items: center; gap: 8px;
    font-weight: 700; font-size: 13px; line-height: 15px; color: var(--partner-ink);
  }
  .partner-name::before {
    content: ""; width: 14px; height: 14px; background: var(--orange); flex: none;
  }
</style>
</head>
<body>
<main class="page">
  <div class="hero-photo" role="img" aria-label="Photograph of a team of health professionals stacking their hands together in a gesture of collaboration"></div>
  <div class="hero-rule top"></div>
  <h1 class="hero-title">REFERRAL PARTNERS REQUIRED</h1>
  <div class="hero-rule bottom"></div>

  <h2 class="section-heading" style="top:40px;">REFERRAL PARTNERS REQUIRED</h2>

  <div class="partner-item" style="top:106px;"><h3>MASSAGE THERAPISTS</h3><p>Deep tissue and remedial massage Therapeutic massage</p></div>
  <div class="partner-item" style="top:165px;"><h3>FASCIAL THERAPISTS</h3><p>Kinetic chain fascial releases to reset the alignment of the whole body</p></div>
  <div class="partner-item" style="top:226px;"><h3>PHYSIOTHERAPISTS</h3><p>Pain relief, protect and strengthen both lower limb and upper limb</p></div>
  <div class="partner-item" style="top:285px;"><h3>GP, SPORTS PHYSICIANS</h3><p>General health, diagnostics, treatment support, prescription medications</p></div>

  <h2 class="section-heading" style="top:346px;">SPECIALIST REFERRALS</h2>

  <div class="partner-item" style="top:391px;"><h3>OSTEOPATHS AND CHIROPRACTORS</h3><p>Mobilisations and manipulative therapy for the spinal column and limbs</p></div>
  <div class="partner-item" style="top:450px;"><h3>DIETICIAN AND NUTRITIONISTS</h3><p>DEXA scan for bone density/lean mass/fat mass<br>Optimising gut health and nutrition - You are what you eat!</p></div>
  <div class="partner-item" style="top:530px;"><h3>PSYCHOLOGISTS/PSYCHIATRISTS</h3><p>Sometimes our physical body cannot get better until we optimise a healthy mind</p></div>
  <div class="partner-item" style="top:589px;"><h3>PERSONAL TRAINERS, PILATES AND YOGA INSTRUCTORS</h3><p>Create awesome body strength, flexibility and resilience</p></div>
  <div class="partner-item" style="top:647px;"><h3>SURGEONS</h3><p>When conservative methods are ineffective, surgical intervention works well.</p></div>

  <div class="partner-bar">
    <span class="partner-name">Northgate Fitness<br>Academy</span>
    <span class="partner-name">Active Sport<br>Council</span>
    <span class="partner-name">Kinetic Lines<br>Institute</span>
    <span class="partner-name">Podiatric Sport<br>Society</span>
  </div>
</main>
</body>
</html>
```